Business card

We need a business card design for our company based in Auckland , New Zealand called 'Ridge + Studio Ltd'. We provide architectural services. We would like to see designs that use the max. three colours (such as white, black, grey) The final design should communicate financial safety and growth."
Also I will provide our company logo. I would like to the logo to be embeded onto our business card.

Target Market(s)

new residential house, alteration & addition & light commericila design & drafting service

Industry/Entity Type

Architecture

Contact Information for Business Card

Company name: ridge + studio Ltd.
Name: Mark Delford
Job title: architectural designer & Design LBP
email address: mark@rplusd.co.nz
mobile number: 02 5163 2290
web site: www.rplusd.co.nz

Requirements
Must have
• My project must have..
• - embeded logo (attached company logo)
• I don't have a bigger version for our company logo, but I have one old one, so you can remove the word from it)
• - insert the attached small BKTW logo & LBP logo
• - creative, simple and clear business card.
• - Max. three colours
Nice to have
• - Here are the samples I would like to share with you: http://www.plimvora.com/blog/minimalistic-business-card-designs/
• I would like to have my business card like one of the creation.
Should not have
• TBA

```html
<!DOCTYPE html>
<html lang="en">
<head>
<meta charset="utf-8">
<title>Ridge + Studio Ltd — Business Card</title>
<link href="https://fonts.googleapis.com/css2?family=PT+Sans:wght@400;700&display=swap" rel="stylesheet">
<style>
  :root {
    --page-bg: #e4e4e4;
    --card-black: #1b1b1b;
    --card-silver: #ececec;
    --ink-white: #f4f4f4;
    --ink-grey: #9a9a9a;
    --ink-dark: #2a2a2a;
    --rule-grey: #6a6a6a;
  }
  * { margin: 0; padding: 0; box-sizing: border-box; }
  html, body {
    width: 1200px;
    height: 950px;
    overflow: hidden;
    background: var(--page-bg);
    font-family: "PT Sans", sans-serif;
  }
  .canvas {
    width: 1200px;
    height: 950px;
    display: flex;
    align-items: center;
    justify-content: center;
    gap: 80px;
  }
  .card {
    border-radius: 4px;
    box-shadow: 0 10px 30px rgba(0,0,0,0.18);
    position: relative;
  }

  /* Front */
  .card-front {
    width: 380px;
    height: 620px;
    background: var(--card-black);
    color: var(--ink-white);
  }
  .brand {
    position: absolute;
    top: 48px;
    right: 44px;
    display: flex;
    align-items: center;
    gap: 12px;
  }
  .brand-dot {
    width: 18px;
    height: 18px;
    border-radius: 50%;
    background: var(--ink-white);
  }
  .brand-name {
    font-size: 20px;
    font-weight: 400;
    letter-spacing: 0.5px;
    color: var(--ink-white);
  }
  .contact {
    position: absolute;
    left: 48px;
    bottom: 52px;
  }
  .person-name {
    font-size: 26px;
    font-weight: 400;
    letter-spacing: 1px;
    text-transform: uppercase;
    line-height: 1.1;
  }
  .job-title {
    font-size: 21px;
    line-height: 1.2;
    margin-top: 4px;
  }
  .divider {
    width: 46px;
    height: 2px;
    background: var(--rule-grey);
    margin: 22px 0 18px;
  }
  .company {
    font-size: 16px;
    font-weight: 700;
    margin-bottom: 4px;
  }
  .detail {
    font-size: 16px;
    line-height: 1.35;
  }

  /* Back */
  .card-back {
    width: 620px;
    height: 380px;
    background: linear-gradient(135deg, #f2f2f2 0%, var(--card-silver) 50%, #dcdcdc 100%);
    display: flex;
    align-items: center;
    justify-content: center;
    gap: 34px;
  }
  .partner-name {
    font-size: 44px;
    font-weight: 700;
    letter-spacing: -1px;
    color: var(--ink-dark);
  }
  .partner-rule {
    width: 1px;
    height: 90px;
    background: var(--ink-grey);
  }
  .badge {
    display: block;
  }
</style>
</head>
<body>
<main class="canvas">
  <section class="card card-front" aria-label="Card front">
    <div class="brand">
      <span class="brand-name">ridge + studio</span>
      <span class="brand-dot"></span>
    </div>
    <div class="contact">
      <p class="person-name">Mark Delford</p>
      <p class="job-title">architectural designer &amp;<br>Design LBP</p>
      <div class="divider"></div>
      <p class="company">ridge + studio Ltd.</p>
      <p class="detail">02 5163 2290</p>
      <p class="detail">mark@rplusd.co.nz</p>
      <p class="detail">www.rplusd.co.nz</p>
    </div>
  </section>

  <section class="card card-back" aria-label="Card back">
    <span class="partner-name">BKTW</span>
    <span class="partner-rule"></span>
    <svg class="badge" width="96" height="96" viewBox="0 0 96 96" role="img" aria-label="Licensed practitioner certification badge">
      <circle cx="48" cy="48" r="46" fill="var(--ink-dark)"/>
    </svg>
  </section>
</main>
</body>
</html>
```